Moon Tot needs ecommerce website design help

We need someone to set up a fully functional website for us. We sell baby bibs, I attached them along with our company logo (MTG: moon tot goods). The bibs are made of 100% silicon, they are safe, light weight, soft, smooth, flexible, dishwasher safe and has funny faces.

Business name: Moon Tot Goods
Elm Hollow, NY 00000
email: MoonTotGoods@mailbox-example.com
tel.: (555) 014-TOTS
website: MoonTotGoods-example.com

Target Market(s)

18-40

Industry/Entity Type

Baby

Coding

Coded - Design and coding required

Number of Pages Required

5+ page

Requirements
Must have
• 1. Pages: Why buy from us, Contact Us, Home page, Products Page, Blog
• 2. Use the colors from our logo for the web design.
• 3. Need a link that will connect visitors to our facebook, instagram, Pinterest and Tumblr account. Would like links on,the top left side of the page
Nice to have
• My Cart page
• 1. On contact us page, we want to include some type of template for the customer to complete. (Ex: name, email address, contact number, optional home address, comments)
• 2. When clients visit our website, we want a capture/pop up for the customer to subscribe to our email list to receive discounts. (Ex. Want 10% off your next order ? Suscribe to our mailing list below and get a 10% off code to use at check out. If they don't want to subscribe, they have the option to select "No Thank You, I want to pay full price).
• 3. On home page have subscribe to our email list.

```html
<!DOCTYPE html>
<html lang="en">
<head>
<meta charset="utf-8">
<title>Moon Tot Goods – Baby Bibs</title>
<link href="https://fonts.googleapis.com/css2?family=Roboto:wght@300;400;500;700&family=Dancing+Script:wght@700&display=swap" rel="stylesheet">
<style>
:root{
  --bg:#eceef0;
  --page:#ffffff;
  --pink:#f06292;
  --orange:#f7a21b;
  --green:#8cc63f;
  --text:#333333;
  --muted:#8a8a8a;
  --line:#e3e3e3;
  --footer:#3b3531;
  --footer-text:#cfc8c2;
  --hero:#f3e9ea;
}
*{box-sizing:border-box;margin:0;padding:0}
html,body{width:788px;height:1200px;overflow:hidden}
body{background:var(--bg);font-family:'Roboto',Arial,sans-serif;color:var(--text);font-size:10px;position:relative}
.page{position:absolute;left:40px;top:10px;width:710px;height:1170px;background:var(--page)}
.brand{position:absolute;left:18px;top:22px;display:flex;align-items:center;gap:8px}
.brand-dot{width:22px;height:22px;border-radius:50%;background:var(--orange)}
.brand-name{font-size:34px;font-weight:700;color:var(--pink);letter-spacing:1px}
.topbar{position:absolute;right:120px;top:18px;text-align:right}
.welcome{color:var(--pink);font-size:10px;margin-bottom:4px}
.toplinks{font-size:8px;color:var(--muted)}
.cart{position:absolute;right:18px;top:16px;width:90px;height:44px;border:1px solid var(--line);padding:5px 7px}
.cart b{display:block;color:var(--pink);font-size:10px;font-weight:500}
.cart span{display:inline-block;margin-top:5px;background:var(--orange);color:#fff;font-size:8px;padding:2px 6px}
.nav{position:absolute;left:0;top:88px;width:710px;height:30px;border-top:1px solid var(--line);border-bottom:1px solid var(--line);display:flex;align-items:center;padding-left:18px}
.nav a{font-size:9px;font-weight:500;color:var(--text);text-decoration:none;padding:0 16px;line-height:29px}
.nav a.active{color:var(--pink);border-bottom:2px solid var(--pink)}
.search{position:absolute;right:18px;top:6px;display:flex}
.search span{width:120px;height:18px;border:1px solid var(--line);font-size:8px;color:var(--muted);padding:4px 6px}
.search i{width:22px;height:18px;background:var(--orange);display:flex;align-items:center;justify-content:center}
.promos{position:absolute;left:18px;top:128px;width:210px}
.promo{height:66px;border-bottom:1px solid var(--line);text-align:right;padding:14px 14px 0 0}
.promo h3{font-size:15px;font-weight:500;color:#555}
.promo p{font-size:7px;color:var(--pink);margin-top:3px;letter-spacing:.3px}
.hero{position:absolute;left:238px;top:128px;width:454px;height:264px;background:linear-gradient(90deg,#f7e8ea 0%,#f2dfe2 45%,#ece3dc 100%)}
.hero-photo{position:absolute;right:0;top:0;width:250px;height:264px;background:linear-gradient(135deg,#f1e7e2,#e6d3cf 60%,#efe4e0)}
.hero-text{position:absolute;left:40px;top:56px;text-align:center;width:160px}
.hero-text small{font-size:9px;color:var(--pink);font-weight:500;letter-spacing:1px}
.hero-text h2{font-family:'Dancing Script',cursive;font-size:34px;color:var(--pink);font-weight:700;line-height:1.1}
.hero-text p{font-size:8px;color:var(--muted)}
.hero-btn{position:absolute;left:70px;top:180px;width:110px;height:26px;background:var(--pink);color:#fff;font-family:'Dancing Script',cursive;font-size:15px;text-align:center;line-height:26px}
.section-title{position:absolute;left:18px;top:432px;font-family:'Dancing Script',cursive;font-size:18px;color:var(--green)}
.arrows{position:absolute;right:18px;top:434px;display:flex;gap:4px}
.arrows i{width:16px;height:16px;border-radius:50%;background:var(--green);display:block}
.arrows i:first-child{background:#cfcfcf}
.rule{position:absolute;left:18px;top:456px;width:674px;height:1px;background:var(--line)}
.products{position:absolute;left:18px;top:470px;width:674px;display:flex;justify-content:space-between}
.card{width:150px}
.card-img{width:150px;height:180px;border:1px solid var(--line);display:flex;align-items:center;justify-content:center}
.card-img div{width:100px;height:120px;border-radius:40px 40px 50px 50px}
.stars{margin-top:12px;font-size:8px;color:var(--orange)}
.stars em{font-style:normal;color:var(--muted);margin-left:8px}
.card h4{font-size:10px;font-weight:400;margin-top:5px;text-align:center}
.price{font-size:14px;color:var(--orange);font-weight:500;text-align:center;margin-top:2px}
.actions{display:flex;gap:4px;margin-top:10px}
.actions span{border:1px solid var(--line);font-size:7px;padding:4px 6px}
.about{position:absolute;left:18px;top:820px;width:440px}
.about h3,.events h3{font-size:14px;font-weight:500;border-bottom:1px solid var(--line);padding-bottom:6px}
.about .lead{color:var(--orange);font-style:italic;font-size:9px;line-height:1.5;margin-top:10px}
.about .body{color:var(--muted);font-size:8px;line-height:1.6;margin-top:8px}
.events{position:absolute;left:478px;top:820px;width:214px}
.event{display:flex;align-items:center;gap:8px;margin-top:14px;font-size:8px;color:var(--muted)}
.event i{width:16px;height:16px;border-radius:50%;background:var(--green);flex:none}
.event b{color:var(--orange);font-weight:400}
.footer{position:absolute;left:0;top:990px;width:710px;height:180px;background:var(--footer);color:var(--footer-text)}
.col{position:absolute;top:18px}
.col h4{color:var(--orange);font-size:10px;font-weight:500;letter-spacing:.5px;margin-bottom:10px}
.col li{list-style:none;font-size:8px;line-height:14px}
.col li::before{content:"› ";color:var(--orange)}
.col p{font-size:8px;line-height:14px}
.field{width:120px;height:18px;background:#fff;font-size:7px;color:var(--muted);padding:5px}
.signup{width:50px;height:18px;background:var(--orange);color:#fff;font-size:8px;text-align:center;line-height:18px;margin-top:6px}
.social{display:flex;gap:6px}
.social i{width:18px;height:18px;border-radius:50%;border:1px solid var(--footer-text);display:block}
.cards{display:flex;gap:4px}
.cards i{width:20px;height:13px;background:#d8d2cc;display:block}
.copy{position:absolute;left:0;bottom:10px;width:710px;text-align:center;font-size:7px;border-top:1px solid #51493f;padding-top:10px}
</style>
</head>
<body>
<div class="page">
  <header>
    <div class="brand"><span class="brand-dot"></span><span class="brand-name">MTG</span></div>
    <div class="topbar">
      <p class="welcome">Welcome to our online store!</p>
      <p class="toplinks">My account | My Wishlist | My Cart | Checkout | Log in</p>
    </div>
    <div class="cart"><b>Shopping Cart</b><span>0 Items - $0.00</span></div>
  </header>

  <nav class="nav">
    <a class="active">HOME</a><a>PRODUCTS</a><a>WHY BUY FROM US</a><a>BLOG</a><a>CONTACT US</a>
    <div class="search"><span>Search here...</span><i><svg width="9" height="9" viewBox="0 0 10 10"><circle cx="4" cy="4" r="3" fill="none" stroke="#fff" stroke-width="1.4"/><path d="M6.3 6.3L9 9" stroke="#fff" stroke-width="1.4"/></svg></i></div>
  </nav>

  <aside class="promos">
    <div class="promo"><h3>New Arrivals</h3><p>GET UP TO 50% OFF</p></div>
    <div class="promo"><h3>Girl Baby Bibs</h3><p>GET UP TO 30% OFF</p></div>
    <div class="promo"><h3>Free Shipping</h3><p>ON ORDERS OVER $99</p></div>
    <div class="promo"><h3>Sale Collections</h3><p>GET UP TO 50% OFF</p></div>
  </aside>

  <section class="hero">
    <div class="hero-photo" role="img" aria-label="Photo of a smiling toddler in a pink dress sitting on a white chair"></div>
    <div class="hero-text"><small>WE SELL</small><h2>Baby Bibs</h2><p>GET UP TO 50% OFF</p></div>
    <div class="hero-btn">Shop Now!</div>
  </section>

  <h2 class="section-title">New Products</h2>
  <div class="arrows"><i></i><i></i></div>
  <div class="rule"></div>

  <section class="products">
    <article class="card"><div class="card-img"><div role="img" aria-label="Pink silicone baby bib with a funny face" style="background:#e94a8a"></div></div><p class="stars">★★★★☆<em>1 Review(s)</em></p><h4>Lovely - baby bibs</h4><p class="price">$34.25</p><div class="actions"><span>Add to Cart</span><span>♡</span><span>⇄</span></div></article>
    <article class="card"><div class="card-img"><div role="img" aria-label="Blue silicone baby bib with a funny face" style="background:#2fa6e0"></div></div><p class="stars">★★★★☆<em>1 Review(s)</em></p><h4>Lovely - baby bibs</h4><p class="price">$34.25</p><div class="actions"><span>Add to Cart</span><span>♡</span><span>⇄</span></div></article>
    <article class="card"><div class="card-img"><div role="img" aria-label="Green silicone baby bib with a funny face" style="background:#5cbf4a"></div></div><p class="stars">★★★★☆<em>1 Review(s)</em></p><h4>Lovely - baby bibs</h4><p class="price">$34.25</p><div class="actions"><span>Add to Cart</span><span>♡</span><span>⇄</span></div></article>
    <article class="card"><div class="card-img"><div role="img" aria-label="Orange silicone baby bib with a funny face" style="background:#f59a1f"></div></div><p class="stars">★★★★☆<em>1 Review(s)</em></p><h4>Lovely - baby bibs</h4><p class="price">$34.25</p><div class="actions"><span>Add to Cart</span><span>♡</span><span>⇄</span></div></article>
  </section>

  <section class="about">
    <h3>About Moon Tot Goods</h3>
    <p class="lead">our soft baby bibs. The bibs are made of 100% silicon, they are safe, light weight, soft, smooth, flexible, dishwasher safe and has funny faces.</p>
    <p class="body">Every bib is designed for busy parents who want easy cleanup after meals. Simply rinse or place in the dishwasher, then roll it up for travel. Our colorful pocket catches crumbs and spills, so little ones can explore new foods with joy while you spend less time wiping tables and more time together.</p>
  </section>

  <section class="events">
    <h3>Events</h3>
    <div class="event"><i></i><span><b>Sale Event for Baby:</b> Get one free bib today</span></div>
    <div class="event"><i></i><span><b>Buy and Save:</b> coupons with every order</span></div>
    <div class="event"><i></i><span><b>Friendly Expert Service:</b> we are here to help</span></div>
  </section>

  <footer class="footer">
    <div class="col" style="left:18px"><h4>USEFUL LINKS</h4><ul><li>Home</li><li>Products</li><li>Why buy from us</li><li>Blog</li><li>Contact us</li></ul></div>
    <div class="col" style="left:160px"><h4>NEWSLETTER SUBSCRIPTION</h4><div class="field">Email Address</div><div class="signup">Join</div></div>
    <div class="col" style="left:360px"><h4>CONTACT INFO</h4><p>Moon Tot Goods</p><p>Elm Hollow, NY 00000</p><p style="margin-top:6px">Email: MoonTotGoods@mailbox-example.com</p><p>Tel: (555) 014-TOTS</p></div>
    <div class="col" style="left:560px"><h4>GET SOCIAL</h4><div class="social"><i></i><i></i><i></i><i></i></div><h4 style="margin-top:16px">PAY THROUGH</h4><div class="cards"><i></i><i></i><i></i><i></i><i></i></div></div>
    <p class="copy">Copyright © 2016, Moon Tot Goods All Right Reserved.</p>
  </footer>
</div>
</body>
</html>
```